Business Card Design

We are a manufacturing and distribution company with most of our customer base being supermarkets. We have established brand guidelines that are attached.

```html
<!DOCTYPE html>
<html lang="en">
<head>
<meta charset="utf-8">
<title>Veltaro Business Card</title>
<link rel="stylesheet" href="https://fonts.googleapis.com/css2?family=Archivo:wght@700;800&family=Arimo:wght@400;700&display=swap">
<style>
  :root {
    --backdrop: #e9e9eb;
    --card-dark: #221f20;
    --card-darker: #151314;
    --pattern-mid: #2c2a2b;
    --pattern-light: #4a4849;
    --brand-red: #e3131b;
    --brand-blue: #0a6ec3;
    --text-white: #ffffff;
    --text-soft: #e6e6e6;
    --rule: #9a9a9a;
  }
  * { box-sizing: border-box; margin: 0; padding: 0; }
  html, body { width: 1200px; height: 802px; overflow: hidden; }
  body {
    background: var(--backdrop);
    font-family: "Arimo", Arial, sans-serif;
    position: relative;
  }
  .card {
    position: absolute;
    width: 540px;
    height: 309px;
    top: 246px;
    overflow: hidden;
    box-shadow: 0 10px 24px rgba(0,0,0,0.22);
  }
  .card--front { left: 40px; background: var(--card-dark); }
  .card--back { left: 620px; background: var(--card-darker); }

  .brand {
    position: absolute;
    display: flex;
    align-items: center;
    gap: 12px;
  }
  .brand__square {
    width: 24px; height: 24px;
    background: var(--brand-red);
  }
  .brand__name {
    font-family: "Archivo", Arial, sans-serif;
    font-weight: 800;
    color: var(--text-white);
    letter-spacing: 0.04em;
    line-height: 1;
  }
  .card--front .brand { left: 36px; top: 62px; }
  .card--front .brand__name { font-size: 32px; }

  .rule-top {
    position: absolute;
    left: 36px; right: 34px; top: 118px;
    height: 1px; background: var(--rule);
  }
  .person { position: absolute; left: 36px; top: 146px; }
  .person__name {
    font-family: "Archivo", Arial, sans-serif;
    font-weight: 700;
    font-size: 17px;
    color: var(--brand-red);
    letter-spacing: 0.03em;
  }
  .person__role { font-size: 13px; color: var(--text-soft); margin-top: 3px; }
  .rule-short {
    position: absolute;
    left: 36px; top: 200px;
    width: 250px; height: 1px; background: var(--rule);
  }
  .contacts {
    position: absolute;
    left: 36px; top: 212px;
    list-style: none;
    font-size: 12.5px;
    color: var(--text-soft);
    display: grid;
    grid-template-columns: auto auto;
    column-gap: 22px;
    row-gap: 6px;
  }
  .contacts li { display: flex; align-items: center; gap: 7px; white-space: nowrap; }
  .contacts .contacts__wide { grid-column: 1 / 3; padding-left: 18px; }
  .contacts svg { width: 11px; height: 11px; flex: none; }

  .edge-band {
    position: absolute; left: 0; right: 0; bottom: 0; height: 9px;
    display: flex;
  }
  .edge-band__red { width: 34px; background: var(--brand-red); }
  .edge-band__blue { flex: 1; background: var(--brand-blue); }

  .pattern-field {
    position: absolute; inset: 0;
    background: linear-gradient(120deg, var(--card-darker) 0%, var(--pattern-mid) 55%, var(--pattern-light) 100%);
  }
  .card--back .brand { left: 190px; top: 196px; }
  .card--back .brand__name { font-size: 30px; }
  .card--back .edge-line {
    position: absolute; left: 0; right: 0; bottom: 0; height: 3px;
    background: var(--brand-red);
  }
</style>
</head>
<body>
  <section class="card card--front" aria-label="Business card front">
    <div class="brand">
      <span class="brand__square"></span>
      <span class="brand__name">VELTARO</span>
    </div>
    <div class="rule-top"></div>
    <div class="person">
      <p class="person__name">MARCUS HALE</p>
      <p class="person__role">Manager</p>
    </div>
    <div class="rule-short"></div>
    <ul class="contacts">
      <li>
        <svg viewBox="0 0 12 12" aria-hidden="true"><path d="M2.5 1 L4.5 1 L5 3.5 L3.8 4.4 C4.5 6 5.8 7.4 7.5 8.2 L8.5 7 L11 7.5 L11 9.5 C11 10.4 10.3 11 9.5 11 C5 10.6 1.4 7 1 2.5 C1 1.7 1.6 1 2.5 1 Z" fill="var(--brand-red)"/></svg>
        555-014-2280
      </li>
      <li>
        <svg viewBox="0 0 12 12" aria-hidden="true"><circle cx="6" cy="6" r="5" fill="none" stroke="var(--brand-red)" stroke-width="1.2"/><path d="M1 6 H11 M6 1 C3.5 3.5 3.5 8.5 6 11 M6 1 C8.5 3.5 8.5 8.5 6 11" fill="none" stroke="var(--brand-red)" stroke-width="1"/></svg>
        www.veltarofoods.com
      </li>
      <li>
        <svg viewBox="0 0 12 12" aria-hidden="true"><rect x="1" y="2.5" width="10" height="7" fill="none" stroke="var(--brand-red)" stroke-width="1.2"/><path d="M1 2.5 L6 6.5 L11 2.5" fill="none" stroke="var(--brand-red)" stroke-width="1.2"/></svg>
        m.hale@veltaromail.com
      </li>
      <li></li>
      <li class="contacts__wide">48 Mill Lane, Dorrow, OH 45010</li>
    </ul>
    <div class="edge-band">
      <span class="edge-band__red"></span>
      <span class="edge-band__blue"></span>
    </div>
  </section>

  <section class="card card--back" aria-label="Business card back">
    <div class="pattern-field" role="img" aria-label="Embossed repeating diamond brand pattern in dark grey tones"></div>
    <div class="brand">
      <span class="brand__square"></span>
      <span class="brand__name">VELTARO</span>
    </div>
    <div class="edge-line"></div>
  </section>
</body>
</html>
```